Geschäftspapiere für Jobwebseite
Zielgruppe
Hier finden sie alle Informationen zu unserem Unternehmen:
https://www.sauberwerk-stelle.com
Aufgabenstellung
Gerne von den Farben angelehnt an die Website ein modernes Briefpapier gestalten.

```html
<!DOCTYPE html>
<html lang="de">
<head>
<meta charset="utf-8">
<title>Briefpapier – Sauberwerk-Stelle</title>
<link rel="stylesheet" href="https://fonts.googleapis.com/css2?family=Poppins:wght@400;500;600;700&display=swap">
<style>
  :root {
    --green: #10a045;
    --dark: #3c3d4a;
    --text: #3a3a3a;
    --muted: #555;
    --rule: #4a4a4a;
    --paper: #ffffff;
    --backdrop: #d3d3d1;
  }
  * { margin: 0; padding: 0; box-sizing: border-box; }
  html, body {
    width: 989px; height: 1200px; overflow: hidden;
    background: var(--backdrop);
    font-family: "Poppins", sans-serif;
    color: var(--text);
  }
  .sheet {
    position: absolute; left: 70px; top: 0;
    width: 848px; height: 1200px;
    background: var(--paper);
  }
  .top-band { position: absolute; left: 0; top: 0; width: 100%; height: 9px; background: var(--green); }
  .brand {
    position: absolute; left: 47px; top: 52px;
    font-weight: 700; font-size: 31px; letter-spacing: -0.5px;
    color: var(--dark);
    display: flex; align-items: center; gap: 10px;
  }
  .brand-dot { width: 14px; height: 14px; border-radius: 50%; background: var(--green); }
  .sender-line {
    position: absolute; left: 38px; top: 158px;
    font-size: 11.5px; font-weight: 600; color: var(--muted);
  }
  .header-divider { position: absolute; left: 538px; top: 23px; width: 2px; height: 148px; background: var(--rule); }
  .contact { position: absolute; left: 568px; top: 0; }
  .contact-item { position: absolute; left: 0; display: flex; align-items: center; gap: 8px; width: 260px; }
  .contact-item svg { flex: none; width: 26px; height: 26px; }
  .contact-item p { font-size: 13.5px; line-height: 18px; color: var(--muted); }
  .item-phone { top: 36px; }
  .item-address { top: 86px; }
  .item-web { top: 128px; }
  .footer-band { position: absolute; left: 0; bottom: 0; width: 100%; height: 30px; background: var(--green); }
  .footer-tab { position: absolute; right: 0; bottom: 18px; width: 262px; height: 38px; }
  .footer-tab span {
    position: absolute; right: 28px; top: 8px;
    color: #fff; font-weight: 600; font-size: 15px;
  }
  .footer-info { position: absolute; font-size: 11.5px; line-height: 18px; color: var(--muted); }
  .tax { left: 38px; top: 1126px; }
  .bank { left: 150px; top: 1119px; }
  .account { left: 345px; top: 1119px; line-height: 29px; }
  .footer-divider { position: absolute; top: 1116px; width: 2px; height: 54px; background: var(--rule); }
  .div-a { left: 139px; }
  .div-b { left: 334px; }
</style>
</head>
<body>
<main class="sheet">
  <div class="top-band"></div>

  <header>
    <div class="brand"><span>SAUBERWERK-STELLE.com</span><span class="brand-dot"></span></div>
    <p class="sender-line">Jonas Albrecht Immobilien / Lindenhofer Str. 12 / D-40721 Hilden</p>
    <div class="header-divider"></div>

    <div class="contact">
      <div class="contact-item item-phone">
        <svg viewBox="0 0 26 26" aria-hidden="true"><circle cx="13" cy="13" r="11.5" fill="none" stroke="#3c3d4a" stroke-width="2"/><path d="M9 7.5l2.2 2.8-1.3 1.6c.9 1.8 2.3 3.2 4.1 4.1l1.6-1.3 2.8 2.2-1.4 2c-4.8-.7-8.8-4.7-9.5-9.5z" fill="#10a045"/></svg>
        <p>+02 4180 3276<br>+02 4180 3276</p>
      </div>
      <div class="contact-item item-address">
        <svg viewBox="0 0 26 26" aria-hidden="true"><circle cx="13" cy="13" r="11.5" fill="none" stroke="#3c3d4a" stroke-width="2"/><path d="M13 6a5 5 0 0 0-5 5c0 3.5 5 9 5 9s5-5.5 5-9a5 5 0 0 0-5-5z" fill="#10a045"/><circle cx="13" cy="11" r="1.8" fill="#fff"/></svg>
        <p>12, Harbor Point,<br>77 Boston, MA 02110</p>
      </div>
      <div class="contact-item item-web">
        <svg viewBox="0 0 26 26" aria-hidden="true"><circle cx="13" cy="13" r="11.5" fill="none" stroke="#3c3d4a" stroke-width="2"/><circle cx="13" cy="13" r="7" fill="#10a045"/><path d="M6 13h14M13 6v14M8 9h10M8 17h10" stroke="#fff" stroke-width="1"/></svg>
        <p>info@sauberwerk-stelle.com<br>www.sauberwerk-stelle.com</p>
      </div>
    </div>
  </header>

  <footer>
    <p class="footer-info tax">Steuer-Nr.<br>DE418207735</p>
    <div class="footer-divider div-a"></div>
    <p class="footer-info bank">Bankverbindung:<br>Stadtsparkasse Rheinberg</p>
    <div class="footer-divider div-b"></div>
    <p class="footer-info account">BIC RHBGDE33XXX<br>IBAN DE71 3105 0000 0004 2287 19</p>

    <div class="footer-band"></div>
    <div class="footer-tab">
      <svg width="262" height="38" viewBox="0 0 262 38" aria-hidden="true">
        <path d="M0 38 C10 38 12 0 30 0 H262 V38 Z" fill="#3c3d4a"/>
        <path d="M0 38 C10 38 12 0 30 0" fill="none" stroke="#fff" stroke-width="3"/>
      </svg>
      <span>www.albrecht-immobilien.de</span>
    </div>
  </footer>
</main>
</body>
</html>
```